Business card for new business

I need a card with fruit and an island vibe. The name of our business is called Coral Dash. The graphics we are getting on our truck is a wave of Fruit with an island beach back ground. The wave is made of fruit and its breaking on the shore of an island with palm trees. We also would like our logo some how put on the card. The back of the card to have our slogan. with an island back ground. Our slogan is Fresh energy, ready when you are.

Target Market(s)

Athletes, people who workout, sporting events

Contact Information for Business Card

fruit and island is the theme of the card

Font styles to use
Sans Serif

Requirements
Must have
• I need colors to be bright. Fruit must look realistic. Pineapple, coconut, watermelon, strawberry, bananas, kiwi, mango should be among the fruit. Logo should be put on card somehow. back of card should have our slogan. "Fresh energy, ready when you are".
Nice to have
• If you could please make a wave crashing on the shore of a island beach with palm trees in the back ground.

```html
<!DOCTYPE html>
<html lang="en">
<head>
<meta charset="utf-8">
<title>Coral Dash – Business Card</title>
<link rel="stylesheet" href="https://fonts.googleapis.com/css2?family=Roboto:wght@400;500&display=swap">
<style>
  :root {
    --stage: #2e2e30;
    --green: #1f6e52;
    --green-dark: #165a42;
    --white: #ffffff;
    --lime: #e8ea6c;
    --sky: #2e5c78;
    --sea: #5e8fa0;
    --sea-light: #8fb3bd;
    --text-light: #f2f5f3;
  }
  * { margin: 0; padding: 0; box-sizing: border-box; }
  html, body { width: 1200px; height: 896px; overflow: hidden; }
  body {
    background: var(--stage);
    font-family: "Roboto", sans-serif;
    display: flex;
    align-items: center;
    justify-content: center;
    gap: 40px;
  }
  .card {
    position: relative;
    width: 560px;
    height: 320px;
    border-radius: 18px;
    overflow: hidden;
  }

  /* Back side */
  .card-back .island-photo {
    position: absolute; inset: 0;
    background: linear-gradient(180deg, var(--sky) 0%, #3f7386 38%, var(--sea) 60%, var(--sea-light) 100%);
  }
  .card-back .brand-badge {
    position: absolute;
    left: 50%; top: 40%;
    transform: translate(-50%, -50%);
    width: 150px; height: 150px;
    border-radius: 50%;
    border: 4px solid var(--white);
    display: flex; align-items: center; justify-content: center;
  }
  .card-back .brand-name {
    color: var(--white);
    font-weight: 500;
    font-size: 17px;
    letter-spacing: 0.5px;
  }
  .card-back .slogan {
    position: absolute;
    left: 0; right: 0; bottom: 40px;
    text-align: center;
    color: var(--lime);
    font-size: 20px;
    font-weight: 400;
  }

  /* Front side */
  .card-front { background: var(--green); }
  .card-front .panel { position: absolute; inset: 0; }
  .card-front .logo-area {
    position: absolute;
    right: 52px; top: 36px;
    width: 196px; height: 196px;
    border-radius: 50%;
    border: 12px solid var(--green);
    display: flex; align-items: center; justify-content: center;
  }
  .card-front .brand-name {
    color: var(--green);
    font-weight: 500;
    font-size: 22px;
    letter-spacing: 0.5px;
  }
  .card-front .contact {
    position: absolute;
    left: 34px; bottom: 30px;
    color: var(--text-light);
  }
  .contact .person-name {
    color: var(--lime);
    font-size: 26px;
    font-weight: 400;
    letter-spacing: 0.5px;
    text-transform: uppercase;
  }
  .contact .role { font-size: 15px; margin-bottom: 14px; }
  .contact .address { font-size: 15px; line-height: 1.35; margin-bottom: 12px; }
  .contact .lines { list-style: none; font-size: 15px; line-height: 1.4; }
  .contact .lines li { display: flex; align-items: center; gap: 8px; }
  .contact .lines svg { width: 11px; height: 11px; flex: none; }
</style>
</head>
<body>

  <section class="card card-back" aria-label="Card back">
    <div class="island-photo" role="img" aria-label="Photo of a tropical island with palm trees over calm turquoise sea"></div>
    <div class="brand-badge"><span class="brand-name">CORAL DASH</span></div>
    <p class="slogan">Fresh energy, ready when you are</p>
  </section>

  <section class="card card-front" aria-label="Card front">
    <svg class="panel" viewBox="0 0 560 320" preserveAspectRatio="none" aria-hidden="true">
      <path d="M250 0 C210 90 240 230 360 272 C440 298 520 280 560 262 L560 0 Z" fill="var(--lime)"/>
      <path d="M262 0 C222 90 250 222 366 260 C444 284 520 268 560 250 L560 0 Z" fill="var(--white)"/>
    </svg>
    <div class="logo-area"><span class="brand-name">CORAL DASH</span></div>
    <div class="contact">
      <h1 class="person-name">Dana Reyes</h1>
      <p class="role">Director</p>
      <p class="address">518 Harbor Lane<br>Bay Point, TX 70000</p>
      <ul class="lines">
        <li>
          <svg viewBox="0 0 12 12"><path d="M2.5 1 L4.5 1 L5.3 3.5 L4 4.5 C4.6 6 6 7.4 7.5 8 L8.5 6.7 L11 7.5 L11 9.5 C11 10.3 10.3 11 9.5 11 C5 11 1 7 1 2.5 C1 1.7 1.7 1 2.5 1 Z" fill="var(--lime)"/></svg>
          1234 555 0147
        </li>
        <li>
          <svg viewBox="0 0 12 12"><rect x="1" y="2.5" width="10" height="7" fill="none" stroke="var(--lime)" stroke-width="1.2"/><path d="M1 2.5 L6 6.5 L11 2.5" fill="none" stroke="var(--lime)" stroke-width="1.2"/></svg>
          info@coraldash.com
        </li>
        <li>
          <svg viewBox="0 0 12 12"><circle cx="6" cy="6" r="5" fill="none" stroke="var(--lime)" stroke-width="1.2"/><path d="M1 6 H11 M6 1 C3.5 3.5 3.5 8.5 6 11 M6 1 C8.5 3.5 8.5 8.5 6 11" fill="none" stroke="var(--lime)" stroke-width="1"/></svg>
          www.coraldash.com
        </li>
      </ul>
    </div>
  </section>

</body>
</html>
```